Government Contracting business needs a website design.

Pellworth & Quine, LLC is a minority owned Service Disabled Veteran Owned Small Business (SDVOSB) that provides Strategic Planning, Public Health Emergency Response, and Data Management Solutions for Federal Civilian and Defense Agencies. We have over 20 years of experience helping health and defense agencies develop concept of operations, deploy assets and personnel in Hot Zones around the world, and deliver goods and services all of the globe.

We are a leader in the field of Data Management. We help our customers develop cloud migration and disaster recovery strategies. We are experts with database management, data replication, queries, consolidation, and records management.

We are looking for a very nice and simple website designs that states clearly what we do as a company and that is easy for our customers to follow. We would like to have some moving pictures that are base on our expertise. We want the website to be easy to use and have the scroll down features that keeps things all on the same page when clicking on the menu. I attached a document with what we need on the website. I will also attach our logo. We want it to look simple clean and very professional.

Target Market(s)

Government Contracting, Management Consulting, Health

Industry/Entity Type

Government

Coding

Coded - Design and coding required

Number of Pages Required

1 page

Font styles to use
Serif

Requirements
Must have
• Very nice picture slides that speaks to our capabilities in Disaster Response, Strategic Planning, and Database Management. Slick look and design. Make sure SDVOSB Logo is right at the beginning of website as our customers is looking for that certification. Very nice colors that blend well with our logo.
Nice to have
• Very nice and slick colors that blends well with logo.
Should not have
• Basic website design that are weary on the eye. No bright colors, just simple colors that looks good with logo.

```html
<!DOCTYPE html>
<html lang="en">
<head>
<meta charset="utf-8">
<title>Pellworth & Quine, LLC</title>
<link href="https://fonts.googleapis.com/css2?family=Libre+Baskerville:wght@400;700&family=Work+Sans:wght@400;500;600&display=swap" rel="stylesheet">
<style>
:root{
  --navy:#1c3a86;
  --navy-deep:#0b1a3a;
  --slate:#2f4c5c;
  --slate-dark:#1f3a48;
  --ink:#2a2f33;
  --grey:#6f7478;
  --mist:#eef1f3;
  --panel:#e4edf1;
  --partner-bg:#e2ecf0;
  --white:#ffffff;
  --serif:'Libre Baskerville', Georgia, serif;
  --sans:'Work Sans', Arial, sans-serif;
}
*{box-sizing:border-box;margin:0;padding:0}
html,body{width:1200px;height:3644px;overflow:hidden}
body{position:relative;background:var(--white);font-family:var(--sans);color:var(--ink)}
.abs{position:absolute}
svg.band{position:absolute;left:0;display:block}

/* Hero */
.hero{left:0;top:0;width:1200px;height:760px;background:linear-gradient(100deg,#2550a8 0%,var(--navy) 45%,#142a5e 75%,var(--navy-deep) 100%)}
.brand{left:85px;top:30px;display:flex;align-items:center;gap:12px;color:var(--white)}
.brand-mark{width:48px;height:48px;border:2px solid var(--white);border-radius:50%}
.brand-name{font-family:var(--serif);font-size:24px;line-height:1.1}
.brand-name small{display:block;font-size:10px;font-family:var(--sans);opacity:.85}
.nav{left:452px;top:48px;display:flex;gap:30px;font-family:var(--serif);font-size:15px;color:var(--white)}
.hero-title{left:85px;top:280px;color:var(--white);font-family:var(--serif)}
.hero-title h1{font-size:37px;font-weight:400;margin-bottom:16px}
.hero-title p{font-size:25px;line-height:44px}
.dots{left:85px;top:442px;display:flex;gap:5px}
.dots span{width:12px;height:12px;border:2px solid var(--white);border-radius:50%}
.dots span.on{background:var(--white)}
.hero-art{left:620px;top:95px;width:470px;height:420px;border-radius:28px;
  background:
    radial-gradient(ellipse 120px 150px at 72% 28%,#5bb6ee 0%,rgba(60,140,220,.6) 55%,rgba(60,140,220,0) 100%),
    radial-gradient(ellipse 150px 90px at 34% 62%,#4a8fd8 0%,rgba(40,110,200,.55) 60%,rgba(40,110,200,0) 100%),
    radial-gradient(ellipse 130px 70px at 62% 78%,#2fc3c8 0%,rgba(40,180,200,.4) 55%,rgba(40,180,200,0) 100%),
    linear-gradient(150deg,rgba(40,90,170,.55),rgba(20,50,110,.35));
  border:1px solid rgba(120,180,240,.25)}
.cert{left:1015px;top:255px;width:150px;height:150px;border-radius:50%;
  background:radial-gradient(circle,var(--white) 0 44%,#3763b8 45% 49%,var(--white) 50% 60%,#c8d2e6 61% 64%,var(--white) 65%);
  border:6px solid #d8dfe9;box-shadow:0 4px 14px rgba(0,0,0,.25)}
.hero-logo{left:520px;top:578px;width:160px;height:160px;border-radius:50%;background:var(--slate);border:7px solid var(--white);display:flex;align-items:center;justify-content:center;text-align:center;color:var(--white);font-family:var(--serif);font-size:15px;line-height:1.3}

/* Welcome */
.photo-frame{left:72px;top:905px;width:412px;height:358px;background:#c9cdd1}
.photo{left:85px;top:890px;width:412px;height:360px;background:linear-gradient(135deg,#7a8a9a,#c4c0b8 55%,#5b6a55)}
.welcome{left:543px;top:895px;width:570px}
.welcome h2{font-family:var(--serif);font-weight:400;font-size:33px;white-space:nowrap;color:var(--slate);margin-bottom:16px}
.welcome p{font-size:14.5px;line-height:21px;color:var(--grey);margin-bottom:20px}
.btn{display:inline-block;background:var(--slate);color:var(--white);font-weight:600;font-size:15px;padding:13px 28px}

/* Capabilities */
.cap-title{left:0;top:1458px;width:1200px;text-align:center;font-family:var(--serif);font-size:36px;font-weight:400;color:var(--ink)}
.cap-title span{color:var(--slate)}
.card{top:1528px;width:290px;height:350px;background:var(--white);text-align:center;box-shadow:0 2px 8px rgba(0,0,0,.06)}
.card .img{height:165px}
.card h3{font-size:15px;font-weight:600;color:#555;margin:30px 0 12px}
.card p{font-size:12.5px;line-height:19px;color:#888;padding:0 24px}
.card .more{display:block;font-size:12px;color:#666;margin-top:22px}

/* Join */
.join-title{left:0;top:2190px;width:1200px;text-align:center;font-family:var(--serif);font-size:36px;font-weight:400}
.join-copy{left:230px;top:2252px;width:740px;text-align:center;font-size:13.5px;line-height:20px;color:var(--grey)}
.jobs{left:152px;top:2356px;width:896px;height:345px;background:var(--panel)}
.jobs h3{text-align:center;font-family:var(--serif);font-weight:400;font-size:22px;color:var(--slate);margin:32px 0 22px}
.job{margin:0 40px 13px;height:44px;background:var(--white);display:flex;align-items:center;padding:0 14px 0 30px;font-weight:600;font-size:16px;border:1px solid #d6dee2}
.job .name{flex:1}
.job .b{font-size:12px;font-weight:600;color:var(--white);background:var(--slate);width:98px;height:28px;display:flex;align-items:center;justify-content:center;margin-left:12px}

/* Partners */
.partners-title{left:0;top:2862px;width:1200px;text-align:center;font-family:var(--serif);font-size:36px;font-weight:400;color:var(--slate)}
.partner{top:2942px;height:100px;background:var(--white);border:1px solid #cfd9de;display:flex;align-items:center;justify-content:center;font-family:var(--serif);font-size:21px;white-space:nowrap;color:var(--slate)}

/* Footer */
.seal{top:3200px;width:100px;height:100px;border-radius:50%;background:#3a4a32;border:4px solid #c9b46a}
.seal.sq{border-radius:0;width:170px;background:var(--white);border:none}
.foot-logo{left:82px;top:3260px;width:280px;height:280px;border-radius:50%;background:var(--slate-dark);border:8px solid var(--white);display:flex;align-items:center;justify-content:center;text-align:center;color:var(--white);font-family:var(--serif);font-size:26px;line-height:1.35}
.foot-col{top:3340px;color:var(--white);font-size:13px}
.foot-col h4{font-family:var(--serif);font-weight:400;font-size:18px;margin-bottom:22px}
.contact li{list-style:none;display:flex;gap:14px;line-height:20px;margin-bottom:18px}
.contact svg{flex:none;margin-top:3px}
.links li{list-style:none;line-height:21px}
.links li::before{content:"> ";opacity:.8}
.field{width:212px;height:38px;border:1px solid var(--white);padding:10px 14px;font-size:12px;margin-bottom:12px}
.submit{width:212px;height:38px;background:#4c6573;border:1px solid var(--white);display:flex;align-items:center;justify-content:center;font-weight:600;font-size:15px}
.copyright{left:85px;top:3588px;font-size:13px;color:var(--white)}
.social{left:920px;top:3580px;display:flex;gap:8px}
.social span{width:32px;height:32px;border-radius:50%;background:#4a6fb0}
.social span:nth-child(2){background:#3aa4e0}
.social span:nth-child(3){background:#d84a3a}
.social span:nth-child(4){background:#cc2a2a}
.social span:nth-child(5){background:#b03a8a}
</style>
</head>
<body>

<div class="abs hero"></div>
<div class="abs hero-art" role="img" aria-label="Illustration of server racks, a laptop, coins and a glowing data network"></div>
<div class="abs cert" role="img" aria-label="SDVOSB certification seal"></div>

<div class="abs brand">
  <span class="brand-mark"></span>
  <div class="brand-name">Pellworth &amp; Quine<small>A Health IT Company</small></div>
</div>
<nav class="abs nav"><span>Home</span><span>About</span><span>Services</span><span>Our Team</span><span>Our Partners</span><span>Join Us</span><span>Contact Us</span></nav>

<div class="abs hero-title">
  <h1>Pellworth &amp; Quine, LLC</h1>
  <p>Mission Oriented Health It And Acquisition<br>For The Defense And VA Community</p>
</div>
<div class="abs dots"><span></span><span></span><span class="on"></span><span></span><span></span></div>

<svg class="band" style="top:520px" width="1200" height="340" viewBox="0 0 1200 340">
  <path d="M0 120 C300 210 420 60 640 70 C860 80 1000 -20 1200 60 L1200 340 L0 340Z" fill="#3c5c6c"/>
  <path d="M0 200 C300 280 420 140 640 140 C860 140 1000 60 1200 120 L1200 340 L0 340Z" fill="var(--slate)"/>
  <path d="M0 250 C300 310 420 220 640 210 C860 200 1000 140 1200 200 L1200 340 L0 340Z" fill="var(--white)"/>
</svg>
<div class="abs hero-logo">Pellworth<br>&amp; Quine</div>

<div class="abs photo-frame"></div>
<div class="abs photo" role="img" aria-label="Photo of a service member at a desk in front of a flag"></div>
<div class="abs welcome">
  <h2>Welcome to Pellworth &amp; Quine</h2>
  <p>Pellworth &amp; Quine, LLC is a minority owned Service Disabled Veteran Owned Small Business (SDVOSB) that provides Strategic Planning, Public Health Emergency Response, and Data Management Solutions for Federal Civilian and Defense Agencies. We have over 20 years of experience helping health and defense agencies develop concept of operations, deploy assets and personnel in Hot Zones around the world, and deliver goods and services all of the globe.</p>
  <p>We are a leader in the field of Data Management. We help our customers develop cloud migration and disaster recovery strategies. We are ex-</p>
  <span class="btn">Read More</span>
</div>

<svg class="band" style="top:1230px" width="1200" height="960" viewBox="0 0 1200 960">
  <path d="M0 160 C260 80 420 130 620 80 C820 30 980 20 1200 0 L1200 820 C1000 930 800 800 600 860 C400 920 200 900 0 860Z" fill="var(--mist)"/>
</svg>
<h2 class="abs cap-title">Core <span>Capabilities</span></h2>
<div class="abs card" style="left:140px">
  <div class="img" role="img" aria-label="Strategy planning graphic" style="background:linear-gradient(135deg,#5fd0a8,#3aa985)"></div>
  <h3>Strategic Planning</h3>
  <p>Sed ut perspiciatis unde omnis iste natus error sit voluptatem accusantium doloremque laudantium, totam rem aperiam, eaque ipsa</p>
  <span class="more">Learn More</span>
</div>
<div class="abs card" style="left:453px">
  <div class="img" role="img" aria-label="Photo of an emergency call box on a street" style="background:linear-gradient(135deg,#5d7a4a,#b8483e 50%,#8a8a80)"></div>
  <h3>Public Health Emergency Response</h3>
  <p>Sed ut perspiciatis unde omnis iste natus error sit voluptatem accusantium doloremque laudantium, totam rem aperiam, eaque ipsa</p>
  <span class="more">Learn More</span>
</div>
<div class="abs card" style="left:770px">
  <div class="img" role="img" aria-label="Database technology graphic" style="background:linear-gradient(135deg,#0e1e3a,#2a4f8a 60%,#6aa0d8)"></div>
  <h3>Database Management</h3>
  <p>Sed ut perspiciatis unde omnis iste natus error sit voluptatem accusantium doloremque laudantium, totam rem aperiam, eaque ipsa</p>
  <span class="more">Learn More</span>
</div>

<h2 class="abs join-title">Join Us</h2>
<p class="abs join-copy">Pellworth &amp; Quine strives to provide an outstanding work environment for our employees. We invest in our people and believe strongly in creating an environment where our employees are free to work on innovative solutions that meet our clients' needs. We promote true work-life balance, career advancement, health, and financial security and fun in the work place.</p>
<div class="abs jobs">
  <h3>Job Openings</h3>
  <div class="job"><span class="name">Strategic Planners</span><span class="b">View More</span><span class="b">Apply Now</span></div>
  <div class="job"><span class="name">Program Managers</span><span class="b">View More</span><span class="b">Apply Now</span></div>
  <div class="job"><span class="name">Financial Analysts</span><span class="b">View More</span><span class="b">Apply Now</span></div>
  <div class="job"><span class="name">Health Care Professionals</span><span class="b">View More</span><span class="b">Apply Now</span></div>
</div>

<div class="abs" style="left:0;top:2800px;width:1200px;height:600px;background:var(--partner-bg)"></div>
<h2 class="abs partners-title">Our Partners</h2>
<div class="abs partner" style="left:88px;width:227px">Carrow &amp; Finch</div>
<div class="abs partner" style="left:336px;width:300px">Aldane | Moreth | Kell</div>
<div class="abs partner" style="left:657px;width:213px">Westmark Systems</div>
<div class="abs partner" style="left:890px;width:222px">Halden Dynamics</div>

<svg class="band" style="top:3140px" width="1200" height="504" viewBox="0 0 1200 504">
  <path d="M0 70 C300 160 600 180 860 120 C1020 80 1120 20 1200 0 L1200 504 L0 504Z" fill="#5a7888"/>
  <path d="M0 110 C300 190 600 200 860 150 C1020 120 1120 70 1200 50 L1200 504 L0 504Z" fill="#3c5c6c"/>
  <path d="M0 150 C300 220 600 230 860 190 C1020 165 1120 120 1200 100 L1200 504 L0 504Z" fill="var(--slate-dark)"/>
</svg>
<div class="abs seal" style="left:725px" role="img" aria-label="Partner service seal"></div>
<div class="abs seal" style="left:833px;background:#1d3b7a" role="img" aria-label="Partner service seal"></div>
<div class="abs seal sq" style="left:940px;height:80px;top:3210px" role="img" aria-label="Partner agency badge"></div>

<div class="abs foot-logo">Pellworth<br>&amp; Quine</div>

<div class="abs foot-col" style="left:425px">
  <h4>Contact Info:</h4>
  <ul class="contact">
    <li><svg width="12" height="14" viewBox="0 0 12 14"><path d="M6 0a5 5 0 0 0-5 5c0 4 5 9 5 9s5-5 5-9a5 5 0 0 0-5-5zm0 7a2 2 0 1 1 0-4 2 2 0 0 1 0 4z" fill="#fff"/></svg><span>1187 Linden Crest Rd<br>Marietta, GA</span></li>
    <li><svg width="12" height="12" viewBox="0 0 12 12"><path d="M2 0l3 3-1.5 1.5a7 7 0 0 0 4 4L9 7l3 3-2 2C5 12 0 7 0 2z" fill="#fff"/></svg><span>Tel: 202-555-0143</span></li>
    <li><svg width="13" height="10" viewBox="0 0 13 10"><rect width="13" height="10" fill="#fff"/><path d="M0 0l6.5 5L13 0" stroke="#1f3a48" fill="none"/></svg><span>Mail: info@pellworthquine.com</span></li>
  </ul>
</div>
<div class="abs foot-col" style="left:720px">
  <h4>Quick Links:</h4>
  <ul class="links"><li>Home</li><li>About</li><li>Services</li><li>Our Team</li><li>Join Us</li><li>Contact Us</li></ul>
</div>
<div class="abs foot-col" style="left:898px">
  <h4>Newsletter Signup</h4>
  <div class="field">Email Address</div>
  <div class="submit">SUBMIT</div>
</div>

<div class="abs" style="left:85px;top:3570px;width:1030px;border-top:1px solid rgba(255,255,255,.15)"></div>
<p class="abs copyright">Copyright © 2018. Pellworth &amp; Quine. All rights reserved.</p>
<div class="abs social"><span></span><span></span><span></span><span></span><span></span></div>

</body>
</html>
```